Redesign current business card for food company

i would like to redesign my business card. our company is food company, our product range from chips, juices, milk and etc (mostly dried food stuff).
I want o keep same logo but , the rest is open to new design.
you can check at our website about our company www.orvelpantry.com

Target Market(s)

most of food company

Industry/Entity Type

Business

Contact Information for Business Card

I want to keep more to blue color...

Colors
3176b5
abd036

Requirements
Must have
• our old logo
Nice to have
• we do not mind to have nice material on bus card in order to accomplish nice design. for example: using spot uv, embossed and etc.

```html
<!DOCTYPE html>
<html lang="en">
<head>
<meta charset="utf-8">
<title>Orvel Enterprises Corp. – Business Card</title>
<link href="https://fonts.googleapis.com/css2?family=Open+Sans:wght@400;600;700&display=swap" rel="stylesheet">
<style>
  :root {
    --stage: #e9e7e4;
    --card: #1f2a33;
    --accent-yellow: #ffd21f;
    --accent-gold: #f5b921;
    --brand-blue: #1fb0f0;
    --text-light: #f2f4f5;
  }
  * { margin: 0; padding: 0; box-sizing: border-box; }
  html, body {
    width: 1200px;
    height: 900px;
    overflow: hidden;
    background: var(--stage);
    font-family: "Open Sans", Arial, sans-serif;
  }
  .card {
    position: absolute;
    background: var(--card);
    box-shadow: 0 6px 18px rgba(0,0,0,0.25);
  }
  .card--front { left: 238px; top: 62px; width: 555px; height: 342px; }
  .card--back  { left: 457px; top: 518px; width: 560px; height: 343px; }

  .front-mark {
    position: absolute;
    left: 90px; top: 92px;
    width: 156px; height: 156px;
    border-radius: 50%;
    background: linear-gradient(135deg, var(--accent-gold), var(--accent-yellow));
  }
  .contact-block {
    position: absolute;
    left: 293px; top: 56px;
    color: var(--text-light);
  }
  .person-name {
    font-size: 19px; font-weight: 700;
    color: var(--accent-yellow);
    line-height: 24px;
  }
  .person-title { font-size: 15px; line-height: 20px; }
  .company-name {
    margin-top: 11px;
    font-size: 16px; font-weight: 600;
    color: var(--accent-gold);
    line-height: 22px;
  }
  .address { font-size: 15px; line-height: 23px; }
  .contact-list { list-style: none; margin-top: 9px; }
  .contact-list li {
    display: flex; align-items: center;
    font-size: 15px; line-height: 23px;
  }
  .contact-list svg {
    width: 12px; height: 12px;
    margin-right: 13px;
    fill: var(--accent-yellow);
  }
  .brand-lockup {
    position: absolute;
    left: 0; right: 0; top: 0; bottom: 0;
    display: flex; align-items: center; justify-content: center;
  }
  .brand-name {
    font-size: 112px; font-weight: 700;
    color: var(--brand-blue);
    letter-spacing: -2px;
    line-height: 1;
  }
</style>
</head>
<body>
  <section class="card card--front">
    <div class="front-mark" role="img" aria-label="Brand accent shape"></div>
    <div class="contact-block">
      <p class="person-name">Daniel Harsono</p>
      <p class="person-title">President</p>
      <p class="company-name">Orvel Enterprises Corp.</p>
      <p class="address">482 Birch Ave.Ashford<br>CA 90412</p>
      <ul class="contact-list">
        <li><svg viewBox="0 0 12 12" aria-hidden="true"><path d="M2.4 0.6 4.4 2.8 3.4 4.3C4.2 6 5.8 7.7 7.6 8.6L9.1 7.6 11.4 9.6 10 11.4C5.2 11 1 6.8 0.6 2Z"/></svg>555 014 2288</li>
        <li><svg viewBox="0 0 12 12" aria-hidden="true"><path d="M3 0h5v3H3zM1 4h10v8H1zM3 6h2v1.5H3zM6.5 6h2.5v1.5H6.5zM3 8.5h2V10H3zM6.5 8.5h2.5V10H6.5z"/></svg>555 014 2277</li>
        <li><svg viewBox="0 0 12 12" aria-hidden="true"><path d="M2.5 0h7v12h-7zM3.7 1.3v8h4.6v-8zM5.4 10h1.2v1.2H5.4z" fill-rule="evenodd"/></svg>555 019 4637</li>
        <li><svg viewBox="0 0 12 12" aria-hidden="true"><path d="M0 2h12v8H0zM0.8 2.6 6 6.6 11.2 2.6" /><path d="M0.8 2.6 6 6.6 11.2 2.6" fill="none" stroke="#1f2a33" stroke-width="1"/></svg>Daniel@orvelpantry.com</li>
        <li><svg viewBox="0 0 12 12" aria-hidden="true"><circle cx="6" cy="6" r="5.6"/><path d="M3 3.5 5 3 5.6 5 4 6.4 4.6 8.6 3 8zM7 2.5 9 3.6 8.4 5.4 7 4.6zM7.4 7 9.4 7.2 8 9.6 7 9z" fill="#1f2a33"/></svg>www.orvelpantry.com</li>
      </ul>
    </div>
  </section>

  <section class="card card--back">
    <div class="brand-lockup">
      <span class="brand-name">orvel</span>
    </div>
  </section>
</body>
</html>
```